Business Cards for a law firm

Business cards for our law firm. Use our silhoette logo and OAK PARTNERS - check our website (www.oakpartners.example)

Contact Information for Business Card

our silhouette logo, OAK PARTNERS, 800-555-0147, Dorian Pemberton, dorian@oakpartners.example

Requirements
Must have
• our silhouette logo, OAK PARTNERS, 800-555-0147, Dorian Pemberton, dorian@oakpartners.example

```html
<!DOCTYPE html>
<html lang="en">
<head>
<meta charset="utf-8">
<title>Oak Partners — Business Cards</title>
<link rel="stylesheet" href="https://fonts.googleapis.com/css2?family=Montserrat:wght@600;700&family=Nunito+Sans:wght@400&display=swap">
<style>
  :root {
    --navy: #1c3370;
    --paper: #ffffff;
    --stage: #2b2b30;
    --ink: #1c3370;
  }
  * { box-sizing: border-box; margin: 0; padding: 0; }
  html, body { width: 1200px; height: 801px; overflow: hidden; }
  body {
    background: var(--stage);
    display: flex;
    align-items: center;
    justify-content: center;
    gap: 40px;
  }
  .card {
    width: 540px;
    height: 309px;
    position: relative;
    flex: none;
  }
  .card-front {
    background: var(--navy);
    display: flex;
    align-items: center;
    justify-content: center;
    gap: 18px;
  }
  .brand-mark {
    width: 26px;
    height: 26px;
    background: var(--paper);
  }
  .brand-name {
    font-family: "Montserrat", sans-serif;
    font-weight: 600;
    font-size: 34px;
    letter-spacing: 0.08em;
    color: var(--paper);
  }
  .card-back {
    background: var(--paper);
    color: var(--ink);
    padding: 70px 0 0 92px;
  }
  .firm-title {
    font-family: "Montserrat", sans-serif;
    font-weight: 700;
    font-size: 40px;
    letter-spacing: 0.06em;
    line-height: 1;
  }
  .firm-rule {
    width: 236px;
    height: 3px;
    background: var(--ink);
    margin: 12px 0 18px 140px;
  }
  .contact {
    font-family: "Nunito Sans", sans-serif;
    font-size: 17px;
    line-height: 1.45;
    margin-left: 140px;
  }
  .contact-name { text-transform: uppercase; letter-spacing: 0.04em; }
  .contact-web {
    margin-top: 14px;
    font-size: 13px;
    text-transform: uppercase;
    letter-spacing: 0.28em;
  }
</style>
</head>
<body>
  <section class="card card-front">
    <span class="brand-mark"></span>
    <h1 class="brand-name">OAK PARTNERS</h1>
  </section>

  <section class="card card-back">
    <h2 class="firm-title">OAK PARTNERS</h2>
    <div class="firm-rule"></div>
    <div class="contact">
      <p class="contact-name">Dorian Pemberton</p>
      <p class="contact-phone">800-555-0147</p>
      <p class="contact-email">dorian@oakpartners.example</p>
      <p class="contact-web">www.oakpartners.example</p>
    </div>
  </section>
</body>
</html>
```